Yacht, Boats, Watersports company needs a redesign of business card

Hello Designers!
We are a Boat dealership company that sells fun in the water, we sell boats, Yachts, Kayaks and also yacht WaterSport toys. We are looking to redesign our business cards in to something a little bit more sophisticated. in a way that we can make better use of our company colors. I'm attaching a zipped file containing the company 3 sets of company logo which one is an horizontal another one is a vertical and also a chromed 3d logo. Also is included two set of business cards that we use and also some designs that i think it's interesting. We use PMS 2026c Orange and PMS 7687C Blue. I would like to see at least two different options with the orange as accent and also using blue as an accent color. It's really important for the business cards to have a font option and size that is legible to most people. Our current website is wwww.coralpennant.com. Please visit if you want to have a better feeling of the Boat dealership
You can send Single sided or double side options. We are now using single sided but we may be open for a double side option if we really like the design.
Target Market(s)
Marine, boat sales, yacht sales, water toys sales/
Contact Information for Business Card
Name: Dale Whitcombe
Address: 212 North Fenwick Lane,
Marlow Key, FL 00417
Phone: 555-731-8842
Fax: 555:731-8843
Cell: 555-382-1490
Email: dw@coralpennant.com
Website: coralpennant.com
Requirements
Must have
- the current information of the business card provided.
logo
use the PMS Colors
Nice to have
- a touch of elegance and sophistication but simple
Should not have
- should not have any typography that is hard to read, the card should be simple but yet sophisticated.

```html
<!DOCTYPE html>
<html lang="en">
<head>
<meta charset="utf-8">
<title>Coral Pennant Business Card</title>
<link rel="stylesheet" href="https://fonts.googleapis.com/css2?family=Arimo:wght@400;700&family=Orbitron:wght@700;800&display=swap">
<style>
  :root {
    --stage: #2b2b2b;
    --navy: #0f4a7e;
    --orange: #f26430;
    --paper: #e3e4e5;
    --ink-light: #ffffff;
    --rule: rgba(255, 255, 255, 0.35);
  }
  * { margin: 0; padding: 0; box-sizing: border-box; }
  html, body {
    width: 1093px;
    height: 1200px;
    overflow: hidden;
    background: var(--stage);
  }
  .canvas {
    position: relative;
    width: 1093px;
    height: 1200px;
  }
  .card {
    position: absolute;
    left: 264px;
    width: 580px;
    height: 357px;
  }
  .card--front { top: 226px; background: var(--navy); }
  .card--back { top: 620px; background: var(--paper); }

  .holder-name {
    position: absolute;
    left: 0; right: 0;
    top: 64px;
    text-align: center;
    font-family: "Orbitron", sans-serif;
    font-weight: 800;
    font-size: 20px;
    line-height: 24px;
    letter-spacing: 2px;
    text-transform: uppercase;
    color: var(--orange);
  }
  .divider {
    position: absolute;
    left: 225px;
    width: 128px;
    height: 1px;
    background: var(--rule);
  }
  .divider--top { top: 98px; }
  .divider--bottom { top: 236px; }

  .contact-list, .address {
    position: absolute;
    left: 0; right: 0;
    list-style: none;
    text-align: center;
    font-family: "Arimo", sans-serif;
    font-size: 17px;
    line-height: 20.8px;
    color: var(--ink-light);
  }
  .contact-list { top: 114px; }
  .address { top: 249px; font-style: normal; }
  .label, .web-domain {
    color: var(--orange);
    font-weight: 700;
  }

  .brand-mark {
    position: absolute;
    left: 248px;
    top: 116px;
    width: 86px;
    height: 86px;
  }
  .brand-name {
    position: absolute;
    left: 0; right: 0;
    top: 218px;
    text-align: center;
    font-family: "Orbitron", sans-serif;
    font-weight: 800;
    font-size: 27px;
    line-height: 30px;
    letter-spacing: 5px;
    text-transform: uppercase;
    color: var(--navy);
  }
</style>
</head>
<body>
<main class="canvas">
  <section class="card card--front" aria-label="Business card front">
    <h1 class="holder-name">Dale Whitcombe</h1>
    <div class="divider divider--top"></div>
    <ul class="contact-list">
      <li><span class="label">P:</span> 555-731-8842</li>
      <li><span class="label">F:</span> 555:731-8843</li>
      <li><span class="label">M:</span> 555-382-1490</li>
      <li><span class="label">P:</span> dw@coralpennant.com</li>
      <li>www.<span class="web-domain">coralpennant</span>.com</li>
    </ul>
    <div class="divider divider--bottom"></div>
    <address class="address">
      212 North Fenwick Lane<br>
      Marlow Key, FL 00417
    </address>
  </section>

  <section class="card card--back" aria-label="Business card back">
    <svg class="brand-mark" viewBox="0 0 86 86" aria-hidden="true">
      <circle cx="43" cy="43" r="39" fill="none" stroke="var(--orange)" stroke-width="7"/>
    </svg>
    <p class="brand-name">Coral Pennant</p>
  </section>
</main>
</body>
</html>
```